Verodex business card

Business card for sustainable investment company called "Verodex". Verodex is an exchange platform selling carbon credits between buyers and sellers. Carbon Credits are an environmental commodity for reducing global carbon emissions.

the card should obviously have our logo and the theme should be sustainability/environment mixed with a trading platform.

Contact Information for Business Card

Logo, Name, Title, Phone, Email

Colors
0054AA
0677BA
7BADD7
CADEEF
E8F1F8
0094D4
00A9DD
6FCCEA
C7EBF8
E9F6FB
00AB8E
00BBA5
67D7C9
C6EFE9
E9F9F6
59FF00
82FF00
B8FF75
E3FFCB
F4FFEA

```html
<!DOCTYPE html>
<html lang="en">
<head>
<meta charset="utf-8">
<title>Verodex business card</title>
<link href="https://fonts.googleapis.com/css2?family=Montserrat:wght@600&family=Raleway:wght@400;500;600&display=swap" rel="stylesheet">
<style>
  :root{
    --bg:#ECEFF3;
    --navy:#0D2A52;
    --white:#FFFFFF;
    --blue-deep:#1E6FE8;
    --blue:#1E9BE6;
    --cyan:#2FC8EE;
    --ink:#3A4452;
  }
  *{margin:0;padding:0;box-sizing:border-box}
  html,body{width:1200px;height:977px;overflow:hidden;background:var(--bg)}
  .stage{position:relative;width:1200px;height:977px}
  .card{position:absolute;width:560px;height:320px;border-radius:18px;overflow:hidden;box-shadow:0 14px 30px rgba(13,42,82,.18)}
  .card--front{left:60px;top:90px;background:var(--navy);display:flex;align-items:center;justify-content:center;gap:22px}
  .brand-mark{width:40px;height:40px;border-radius:6px;background:linear-gradient(135deg,var(--cyan),var(--blue-deep))}
  .brand-name{font-family:"Montserrat",sans-serif;font-weight:600;font-size:58px;letter-spacing:2px;color:var(--white)}
  .card--back{left:580px;top:560px;background:var(--white)}
  .back-block{position:absolute;left:0;top:60px;width:260px;height:260px;background:linear-gradient(225deg,var(--blue-deep),var(--cyan))}
  .contact{position:absolute;right:34px;top:70px;text-align:right;font-family:"Raleway",sans-serif}
  .person-name{font-weight:600;font-size:28px;color:var(--blue);letter-spacing:.5px;text-transform:uppercase;line-height:1}
  .person-title{font-weight:400;font-size:17px;color:var(--ink);margin-top:4px}
  .rule{width:42px;height:3px;margin:14px 0 18px auto;background:linear-gradient(90deg,var(--cyan),var(--blue-deep))}
  .details{list-style:none;font-size:15px;color:var(--ink);line-height:1.55}
  .details li{display:flex;align-items:center;justify-content:flex-end;gap:8px}
  .details svg{width:13px;height:13px;flex:none}
</style>
</head>
<body>
<main class="stage">
  <section class="card card--front" aria-label="Card front">
    <span class="brand-mark"></span>
    <span class="brand-name">VERODEX</span>
  </section>

  <section class="card card--back" aria-label="Card back">
    <div class="back-block" role="img" aria-label="Brand colour block"></div>
    <div class="contact">
      <p class="person-name">Marcus Hale</p>
      <p class="person-title">Founder &amp; CEO</p>
      <div class="rule"></div>
      <ul class="details">
        <li>(555) 018-4420
          <svg viewBox="0 0 16 16" aria-hidden="true"><path fill="#1E9BE6" d="M3.5 1.5l2.5 0 1 3.5-1.8 1.2a8 8 0 0 0 4.6 4.6L11 9l3.5 1v2.5c0 1-1 2-2 2A11 11 0 0 1 1.5 3.5c0-1 1-2 2-2z"/></svg>
        </li>
        <li>office@verodex.com
          <svg viewBox="0 0 16 16" aria-hidden="true"><rect x="1" y="3" width="14" height="10" rx="1.5" fill="#1E9BE6"/><path d="M1.5 3.8L8 9l6.5-5.2" stroke="#fff" stroke-width="1.3" fill="none"/></svg>
        </li>
        <li>verodex.com
          <svg viewBox="0 0 16 16" aria-hidden="true"><circle cx="8" cy="8" r="7" fill="#1E9BE6"/><path d="M1 8h14M8 1c-3 3.5-3 10.5 0 14M8 1c3 3.5 3 10.5 0 14" stroke="#fff" stroke-width="1" fill="none"/></svg>
        </li>
      </ul>
    </div>
  </section>
</main>
</body>
</html>
```